Brightwell Aero Services Logo

I need a website and logo for the parent company Brightwell Aero Services, which encompasses general aviation aircraft repair, small aircrat rental and flight school. The company is based in Lawrenceville, Georgia at the Tolleson county airport. A saying that can be incorporated somehere could be, "Quality flying is safe flying", "Safety in mind is no accident" ,. I need a website and logo.

The company started as a repair shop performing repairs and inspections on Harlan, Vantor, Delkin and Ralstead general aviation aircraft, all models of single engine piston, multi engine piston, and single engine turboprop with an emphasis on Harlan Solvane and AeroTurn turbo prop aircraft. We have se=ince entered the aircraft rental and flight instruction market using the Delkin 240 ang Harlan Ranger aircraft.

Number of Pages; I don't know. Maybe 5 ? A home page for Brightwell Aero Services, page for maintenance and repairs and a couple for the rental and school. The maintenance shop is busy, always has been. I need to get the rental and school advertised and busy.

I have a logo for the maintenance shop shirts, not for the school. I do not have the file. I paid a business locally to do that and print on the shirts. They have the file.

Target Market(s)

In our flight school rental fleet department, we are looking for persons wishing to obtain their private pilot license and continuing on into their commercial and instrument ratings. In the aircraft maintenance department, we are looking for new customers who want a better and more quality relationship with their aircraft maintenance provider who will give more detail and quality in the repairs with an emphasis on safety and fewer problems between scheduled maintenance cycles on their aircraft. Brightwell's owner, Dale Hutchins, has been performing aircraft maintenance in the Atlanta area for 27 years. He has built a steady customer base through those years.

```html
<!DOCTYPE html>
<html lang="en">
<head>
<meta charset="utf-8">
<title>Brightwell Aero – Quality Flying Is Safe Flying</title>
<link rel="stylesheet" href="https://fonts.googleapis.com/css2?family=Poppins:wght@400;500;600;700&family=Lato:wght@400;700;900&display=swap">
<style>
:root{
  --green-dark:#173a22;
  --green:#1f4a2b;
  --gold:#a79533;
  --gold-deep:#968529;
  --light:#f8f8f8;
  --cream:#f4f1e9;
  --ink:#1a1a1a;
  --text:#3b3b3b;
  --black:#0b0b0b;
  --white:#ffffff;
}
*{box-sizing:border-box;margin:0;padding:0}
html,body{width:1200px;height:4101px;overflow:hidden}
body{position:relative;background:var(--light);font-family:"Lato",sans-serif;color:var(--text)}
.abs{position:absolute}
.heading{font-family:"Poppins",sans-serif;font-weight:500;color:var(--ink);text-transform:uppercase}
.eyebrow{font-family:"Lato",sans-serif;font-weight:900;letter-spacing:4px;font-size:14px;text-transform:uppercase;color:var(--gold)}
.copy{font-size:14px;line-height:25.5px;color:var(--text)}
.btn{display:flex;align-items:center;justify-content:center;font-family:"Lato",sans-serif;font-weight:900;font-size:14px;text-transform:uppercase;border-radius:26px 26px 4px 26px}
.btn-dark{background:var(--green-dark);color:var(--white)}

/* hero */
.hero{left:0;top:0;width:1200px;height:955px;background:var(--gold);overflow:hidden}
.hero-backdrop{left:0;top:0;width:1200px;height:955px;background:linear-gradient(180deg,#1b4527 0%,#24502f 45%,#1d4428 100%);clip-path:polygon(0 0,1200px 0,1200px 453px,600px 650px,0 453px)}
.hero-gold{left:0;top:0;width:1200px;height:955px;background:linear-gradient(180deg,#a89634 0%,#a49231 100%);clip-path:polygon(0 453px,600px 650px,1200px 453px,1200px 955px,0 955px)}
.brand{left:90px;top:36px;display:flex;align-items:center;gap:12px;font-family:"Poppins",sans-serif;font-weight:600;font-size:26px;color:var(--white);letter-spacing:.5px}
.brand-mark{width:16px;height:16px;background:var(--gold)}
.nav{left:412px;top:52px;display:flex;gap:0;font-family:"Lato",sans-serif;font-size:14px;color:var(--white);text-transform:uppercase}
.nav a{color:var(--white);text-decoration:none;position:absolute;white-space:nowrap}
.nav .active{font-weight:900;border-bottom:2px solid var(--white);padding-bottom:2px}
.call{left:885px;top:43px;width:224px;height:41px;background:var(--white);color:var(--gold);font-weight:900;font-size:13px;border-radius:22px 22px 4px 22px}
.hero-kicker{left:0;top:176px;width:1200px;text-align:center;font-family:"Poppins",sans-serif;font-weight:500;font-size:20px;letter-spacing:3px;color:var(--white)}
.hero-title{left:0;top:212px;width:1200px;text-align:center;font-family:"Poppins",sans-serif;font-weight:700;font-size:51px;color:var(--white);text-transform:uppercase}
.hero-copy{left:250px;top:290px;width:700px;text-align:center;font-size:15px;line-height:26px;color:var(--white);font-weight:700}
.hero-btn{left:517px;top:363px;width:164px;height:46px;background:var(--white);color:var(--gold);font-size:14px}
.hero-plane{left:88px;top:450px;width:1026px;height:250px;border-radius:50% 50% 40% 40%/60% 60% 40% 40%;background:radial-gradient(ellipse at 50% 55%,rgba(255,255,255,.55) 0%,rgba(230,230,225,.35) 35%,rgba(255,255,255,0) 70%)}
.feature{top:764px;width:260px;text-align:center}
.feature svg{display:block;margin:0 auto;width:88px;height:88px}
.feature-label{margin-top:20px;font-family:"Poppins",sans-serif;font-weight:600;font-size:19px;color:var(--white);text-transform:uppercase}

/* about */
.about-photo{background:linear-gradient(160deg,#7c8087 0%,#a3a7ab 45%,#55585e 100%)}
.about-photo-left{left:113px;top:1025px;width:242px;height:417px;border-radius:60px 0 140px 0}
.about-photo-right{left:379px;top:1068px;width:242px;height:417px;border-radius:140px 0 0 0}

/* services */
.services{left:0;top:1558px;width:1200px;height:572px;background:var(--gold)}
.service-card{top:1703px;width:301px;height:350px;overflow:hidden;border-radius:0 80px 80px 0;background:var(--white)}
.service-photo{width:100%;height:294px;border-radius:0 80px 0 0}
.service-label{position:absolute;left:0;bottom:0;width:100%;height:56px;background:var(--white);padding-left:22px;display:flex;align-items:center;font-family:"Poppins",sans-serif;font-weight:600;font-size:16px;color:var(--ink)}

/* rental */
.rental-frame{left:657px;top:2197px;width:440px;height:362px;border-right:4px solid var(--gold);border-bottom:4px solid var(--gold);border-radius:0 0 110px 0}
.rental-photo{left:649px;top:2191px;width:440px;height:360px;border-radius:150px 0 110px 0;background:linear-gradient(180deg,#aab6c0 0%,#c9cfd1 40%,#8c8f7e 62%,#6d7a4a 100%)}

/* partners */
.partner{top:2769px;width:211px;height:135px;background:var(--white);border-radius:16px 0 70px 0;box-shadow:0 6px 20px rgba(0,0,0,.08);display:flex;align-items:center;justify-content:center;gap:10px;font-family:"Poppins",sans-serif;font-weight:600;font-size:28px;color:var(--ink)}
.partner-dot{width:14px;height:14px;background:var(--gold)}

/* contact */
.contact-icon{width:64px;height:64px;border-radius:50%;background:var(--gold);display:flex;align-items:center;justify-content:center}
.contact-label{font-family:"Poppins",sans-serif;font-weight:600;font-size:17px;color:var(--ink);text-transform:uppercase}
.contact-value{font-size:16px;line-height:23px;color:#777}
.form-panel{left:554px;top:3116px;width:535px;height:398px;background:var(--cream)}
.field{background:var(--white);font-family:"Poppins",sans-serif;font-size:14px;color:#555;padding:14px 16px;box-shadow:0 2px 8px rgba(0,0,0,.04)}

/* footer */
.footer{left:0;top:3590px;width:1200px;height:511px;background:var(--black)}
.footer-title{font-family:"Poppins",sans-serif;font-weight:500;font-size:20px;color:var(--white)}
.footer-text{font-size:14px;color:var(--white);line-height:21px}
.footer-list{list-style:none;font-size:14px;color:var(--white)}
.footer-list li{height:27px;display:flex;align-items:center;gap:6px}
.footer-list li::before{content:"→";font-size:11px}
</style>
</head>
<body>

<!-- Hero -->
<section class="abs hero">
  <div class="abs hero-backdrop" role="img" aria-label="Aircraft hangar interior photo tinted dark green"></div>
  <div class="abs hero-gold"></div>
  <div class="abs brand"><span class="brand-mark"></span>BRIGHTWELL AERO</div>
  <nav class="abs nav">
    <a class="active" style="left:0">Home</a>
    <a style="left:104px">About Us</a>
    <a style="left:236px">Services</a>
    <a style="left:365px">Contact</a>
  </nav>
  <div class="abs btn call">Call us: +1 555 014 2290</div>
  <p class="abs hero-kicker">WELCOME TO BRIGHTWELL AERO</p>
  <h1 class="abs hero-title">Quality flying is safe flying</h1>
  <p class="abs hero-copy">Itaque earum rerum hic tenetur a sapiente delectus, ut aut reiciendis voluptatibus maiores alias consequatur aut perferendis doloribus asperiores repellat.</p>
  <div class="abs btn hero-btn">Get Started</div>
  <div class="abs hero-plane" role="img" aria-label="Front view of a white twin-engine propeller aircraft"></div>

  <div class="abs feature" style="left:72px">
    <svg viewBox="0 0 88 88" fill="none" stroke="#fff" stroke-width="3" stroke-linejoin="round"><path d="M44 6c4 0 6 6 6 14v14l28 16v7l-28-9v18l9 7v6l-15-5-15 5v-6l9-7V48l-28 9v-7l28-16V20c0-8 2-14 6-14z"/></svg>
    <p class="feature-label">Aviation Repairs</p>
  </div>
  <div class="abs feature" style="left:335px">
    <svg viewBox="0 0 88 88" fill="none" stroke="#fff" stroke-width="3"><circle cx="44" cy="44" r="38" stroke-dasharray="10 5"/><circle cx="44" cy="44" r="28"/><path d="M32 56l24-24M40 36l14 2-2 14M36 58l-4-6 6 2" stroke-linejoin="round"/></svg>
    <p class="feature-label">Quality Flying</p>
  </div>
  <div class="abs feature" style="left:597px">
    <svg viewBox="0 0 88 88" fill="none" stroke="#fff" stroke-width="3" stroke-linejoin="round"><path d="M8 46h72M30 46c0-6 6-10 14-10s14 4 14 10M44 36v-6M28 58h32M22 70h16M50 70h16"/><path d="M56 18c0-4 4-6 8-5 2-4 9-3 10 2 4 0 5 5 1 6H57c-1 0-1-2-1-3z"/></svg>
    <p class="feature-label">Aviation Rent</p>
  </div>
  <div class="abs feature" style="left:860px">
    <svg viewBox="0 0 88 88" fill="none" stroke="#fff" stroke-width="3" stroke-linejoin="round"><rect x="16" y="8" width="58" height="72"/><path d="M24 8v72M68 14v60"/><circle cx="48" cy="36" r="14"/><path d="M40 44l16-16M34 60h28M34 68h20"/></svg>
    <p class="feature-label">Aviation Schools</p>
  </div>
</section>

<!-- About -->
<section>
  <div class="abs about-photo about-photo-left" role="img" aria-label="Business jet parked on an airport apron"></div>
  <div class="abs about-photo about-photo-right" role="img" aria-label="Business jet taxiing past a hangar"></div>
  <p class="abs eyebrow" style="left:680px;top:1028px">Who we are</p>
  <h2 class="abs heading" style="left:674px;top:1052px;font-size:31px">About Brightwell Aero</h2>
  <p class="abs copy" style="left:676px;top:1096px;width:420px">Nam libero tempore, cum soluta nobis est eligendi optio cumque nihil impedit quo minus id quod maxime placeat facere possimus, omnis voluptas assumenda est, omnis dolor repellendus.</p>
  <p class="abs copy" style="left:676px;top:1224px;width:420px">Temporibus autem quibusdam et aut officiis debitis aut rerum necessitatibus saepe eveniet ut et voluptates repudiandae sint et molestiae non recusandae. Itaque earum rerum hic tenetur a sapiente delectus, ut aut reiciendis voluptatibus maiores alias consequatur aut perferendis doloribus asperiores repellat.</p>
  <div class="abs btn btn-dark" style="left:676px;top:1396px;width:164px;height:48px">Read More</div>
</section>

<!-- Services -->
<section class="abs services"></section>
<p class="abs eyebrow" style="left:0;top:1617px;width:1200px;text-align:center;color:var(--white)">What we offer</p>
<h2 class="abs heading" style="left:0;top:1640px;width:1200px;text-align:center;font-size:31px;color:var(--white)">Our Services</h2>
<div class="abs service-card" style="left:111px">
  <div class="service-photo" role="img" aria-label="Light aircraft under repair inside a hangar" style="background:linear-gradient(170deg,#5b5f63,#9ea2a5 55%,#6f7275)"></div>
  <div class="service-label">Aviation Aircraft Repair</div>
</div>
<div class="abs service-card" style="left:449px">
  <div class="service-photo" role="img" aria-label="High-wing single engine aircraft parked on grass" style="background:linear-gradient(180deg,#8fb0d4,#dfe6ee 50%,#86a15a 72%,#6b8843)"></div>
  <div class="service-label">Small Aircraft Rental</div>
</div>
<div class="abs service-card" style="left:786px">
  <div class="service-photo" role="img" aria-label="Pilot's hands on the controls of a cockpit" style="background:linear-gradient(180deg,#c4c9cf,#a6abb0 45%,#3b3d40 70%,#2a2b2d)"></div>
  <div class="service-label">Small Aircraft Rental</div>
</div>

<!-- Rental & School -->
<section>
  <p class="abs eyebrow" style="left:114px;top:2188px">Aviation</p>
  <h2 class="abs heading" style="left:109px;top:2211px;font-size:31px">Rental and School</h2>
  <p class="abs copy" style="left:111px;top:2254px;width:470px">Nam libero tempore, cum soluta nobis est eligendi optio cumque nihil impedit quo minus id quod maxime placeat facere possimus, omnis voluptas assumenda est, omnis dolor repellendus.</p>
  <p class="abs copy" style="left:111px;top:2356px;width:470px">Temporibus autem quibusdam et aut officiis debitis aut rerum necessitatibus saepe eveniet ut et voluptates repudiandae sint et molestiae non recusandae. Itaque earum rerum hic tenetur a sapiente delectus, ut aut reiciendis voluptatibus maiores alias consequatur aut perferendis doloribus asperiores repellat.</p>
  <div class="abs btn btn-dark" style="left:111px;top:2503px;width:166px;height:48px">Read More</div>
  <div class="abs rental-frame"></div>
  <div class="abs rental-photo" role="img" aria-label="Low-wing training aircraft parked on an airfield ramp"></div>
</section>

<!-- Partners -->
<section>
  <p class="abs eyebrow" style="left:0;top:2683px;width:1200px;text-align:center">Clients</p>
  <h2 class="abs heading" style="left:0;top:2706px;width:1200px;text-align:center;font-size:31px">Our Partners</h2>
  <div class="abs partner" style="left:111px"><span class="partner-dot"></span>Harlan</div>
  <div class="abs partner" style="left:368px"><span class="partner-dot"></span>Vantor</div>
  <div class="abs partner" style="left:622px"><span class="partner-dot"></span>Delkin</div>
  <div class="abs partner" style="left:878px"><span class="partner-dot"></span>Ralstead</div>
</section>

<!-- Contact -->
<section>
  <p class="abs eyebrow" style="left:0;top:3041px;width:1200px;text-align:center">Contact us</p>
  <h2 class="abs heading" style="left:0;top:3064px;width:1200px;text-align:center;font-size:31px">Get in touch with us</h2>
  <h3 class="abs" style="left:113px;top:3138px;font-family:'Poppins',sans-serif;font-weight:500;font-size:25px;color:var(--ink)">Address</h3>

  <div class="abs contact-icon" style="left:115px;top:3184px"><svg width="22" height="28" viewBox="0 0 22 28"><path d="M11 0C5 0 0 5 0 11c0 8 11 17 11 17s11-9 11-17C22 5 17 0 11 0z" fill="#fff"/><circle cx="11" cy="11" r="4" fill="#a79533"/></svg></div>
  <p class="abs contact-label" style="left:196px;top:3182px">Location</p>
  <p class="abs contact-value" style="left:196px;top:3210px">Brightwell Aero<br>United States</p>

  <div class="abs contact-icon" style="left:115px;top:3285px"><svg width="24" height="24" viewBox="0 0 24 24"><path d="M5 2l4 0 2 5-3 2c1 3 4 6 7 7l2-3 5 2v4c0 1-1 2-2 2C10 21 3 14 3 4c0-1 1-2 2-2z" fill="#fff"/></svg></div>
  <p class="abs contact-label" style="left:198px;top:3292px">Phone Number</p>
  <p class="abs contact-value" style="left:198px;top:3320px">+1 555 014 2290</p>

  <div class="abs contact-icon" style="left:115px;top:3382px"><svg width="24" height="18" viewBox="0 0 24 18"><rect width="24" height="18" rx="2" fill="#fff"/><path d="M1 2l11 8 11-8" fill="none" stroke="#a79533" stroke-width="2"/></svg></div>
  <p class="abs contact-label" style="left:198px;top:3389px">Email Address</p>
  <p class="abs contact-value" style="left:198px;top:3417px">hello@brightwellaero.com</p>

  <form class="abs form-panel">
    <div class="abs field" style="left:32px;top:45px;width:237px;height:49px">First Name</div>
    <div class="abs field" style="left:278px;top:45px;width:237px;height:49px">Your Email</div>
    <div class="abs field" style="left:32px;top:108px;width:237px;height:50px">Your Phone</div>
    <div class="abs field" style="left:278px;top:108px;width:237px;height:50px">Address</div>
    <div class="abs field" style="left:32px;top:172px;width:483px;height:110px">Message</div>
    <div class="abs btn btn-dark" style="left:33px;top:312px;width:164px;height:48px">Submit</div>
  </form>
</section>

<!-- Footer -->
<footer class="abs footer">
  <p class="abs" style="left:234px;top:76px;font-family:'Poppins',sans-serif;font-weight:500;font-size:30px;color:var(--white)">Subscribe for Join us</p>
  <div class="abs" style="left:600px;top:75px;width:442px;height:45px;background:var(--white);border-radius:23px;padding-left:23px;display:flex;align-items:center;font-family:'Poppins',sans-serif;font-size:12px;color:#777">Enter Your Email</div>
  <div class="abs btn" style="left:888px;top:78px;width:152px;height:39px;background:var(--gold);color:var(--white);font-family:'Poppins',sans-serif;font-weight:500;letter-spacing:1px;border-radius:20px">Subscribe</div>
  <div class="abs" style="left:111px;top:177px;width:978px;height:1px;background:#555"></div>

  <h4 class="abs footer-title" style="left:113px;top:212px">Contact Us</h4>
  <div class="abs footer-text" style="left:113px;top:263px;display:flex;gap:12px"><svg width="12" height="16" viewBox="0 0 22 28" style="margin-top:3px"><path d="M11 0C5 0 0 5 0 11c0 8 11 17 11 17s11-9 11-17C22 5 17 0 11 0z" fill="#fff"/></svg><span>Brightwell Aero<br>United States</span></div>
  <div class="abs footer-text" style="left:113px;top:318px;display:flex;gap:8px;align-items:center"><svg width="13" height="13" viewBox="0 0 24 24"><path d="M5 2h4l2 5-3 2c1 3 4 6 7 7l2-3 5 2v4c0 1-1 2-2 2C10 21 3 14 3 4c0-1 1-2 2-2z" fill="#fff"/></svg>+1 555 014 2290</div>
  <div class="abs footer-text" style="left:113px;top:353px;display:flex;gap:8px;align-items:center"><svg width="13" height="10" viewBox="0 0 24 18"><rect width="24" height="18" rx="2" fill="#fff"/></svg>hello@brightwellaero.com</div>

  <h4 class="abs footer-title" style="left:419px;top:212px">Quick Links</h4>
  <ul class="abs footer-list" style="left:417px;top:259px">
    <li>Home</li><li>Services</li><li>About Us</li><li>Rental &amp; School</li><li>Contact Us</li>
  </ul>

  <h4 class="abs footer-title" style="left:660px;top:212px">Help Center</h4>
  <ul class="abs footer-list" style="left:660px;top:260px">
    <li>FAQ</li><li>Terms</li><li>Privacy Policy</li><li>Support Center</li><li>Conditions</li>
  </ul>

  <div class="abs" style="left:877px;top:236px;display:flex;align-items:center;gap:10px;font-family:'Poppins',sans-serif;font-weight:600;font-size:19px;color:var(--white)"><span style="width:12px;height:12px;background:var(--gold)"></span>BRIGHTWELL AERO</div>
  <p class="abs footer-text" style="left:877px;top:300px;width:215px;font-size:13px;line-height:22px">We have since entered the aircraft rental and flight instruction market using the Delkin 240 and Harlan Ranger aircraft.</p>

  <div class="abs" style="left:115px;top:454px;width:310px;height:1px;background:#777"></div>
  <p class="abs" style="left:0;top:446px;width:1200px;text-align:center;font-size:11px;color:var(--white)">Copyrights@2023.Brightwell Aero.All Rights Reserved</p>
  <div class="abs" style="left:772px;top:454px;width:317px;height:1px;background:#777"></div>
</footer>

</body>
</html>
```